Veluxa Bone & Motion Business Card

Need a business card using the logo provided. I want brand side of the card to be grey with the logo in the center of the card in white.

On the other side I leave to the designers

Target Market(s)

Personal Injury Attorneys

Industry/Entity Type

Medical

Contact Information for Business Card

Name, CEO. Cell Phone, (Marlowe, Address, Phone) (Homestead, Address, Phone) (Tallahassee, Address, Phone)

Colors

Designer to choose only greyscale colors for use in the design.

Requirements
Must have
• Logo by itself on one side

```html
<!DOCTYPE html>
<html lang="en">
<head>
<meta charset="utf-8">
<title>Veluxa Bone &amp; Motion Business Card</title>
<link rel="stylesheet" href="https://fonts.googleapis.com/css2?family=Montserrat:wght@500;600&family=Nunito:wght@400&display=swap">
<style>
  :root {
    --bg: #1c1c1c;
    --brand-grey: #a6a6a8;
    --brand-grey-light: #b0b0b2;
    --card-white: #ffffff;
    --ink: #1e1e1e;
    --muted: #9a9a9a;
    --line: #a8a8a8;
  }
  html, body {
    margin: 0;
    padding: 0;
    width: 1200px;
    height: 1200px;
    overflow: hidden;
    background: var(--bg);
  }
  .canvas {
    position: relative;
    width: 1200px;
    height: 1200px;
  }
  .card {
    position: absolute;
    left: 260px;
    width: 685px;
    height: 443px;
    box-sizing: border-box;
  }
  .card--front {
    top: 101px;
    background: linear-gradient(200deg, var(--brand-grey-light), var(--brand-grey));
  }
  .card--back {
    top: 626px;
    background: var(--card-white);
  }
  .brand-name {
    margin: 0;
    position: absolute;
    font-family: "Montserrat", sans-serif;
    font-weight: 500;
    text-transform: uppercase;
    text-align: center;
  }
  .brand-name__main,
  .brand-name__sub {
    display: block;
    white-space: nowrap;
  }
  .card--front .brand-name {
    left: 0;
    right: 0;
    top: 160px;
    color: var(--card-white);
  }
  .card--front .brand-name__main {
    font-size: 78px;
    line-height: 90px;
    letter-spacing: 12px;
    margin-right: -12px;
  }
  .card--front .brand-name__sub {
    font-weight: 600;
    font-size: 37px;
    line-height: 44px;
    letter-spacing: 4px;
    margin-right: -4px;
  }
  .card--back .brand-name {
    left: 30px;
    top: 184px;
    width: 268px;
    color: var(--muted);
  }
  .card--back .brand-name__main {
    font-size: 44px;
    line-height: 50px;
    letter-spacing: 6px;
    margin-right: -6px;
  }
  .card--back .brand-name__sub {
    font-weight: 600;
    font-size: 21px;
    line-height: 26px;
    letter-spacing: 3px;
    margin-right: -3px;
  }
  .divider {
    position: absolute;
    left: 342px;
    top: 150px;
    width: 1px;
    height: 140px;
    background: var(--line);
  }
  .person {
    position: absolute;
    left: 397px;
    top: 74px;
  }
  .person__name {
    margin: 0;
    font-family: "Montserrat", sans-serif;
    font-weight: 600;
    font-size: 32px;
    letter-spacing: 5px;
    color: var(--ink);
    line-height: 1.1;
  }
  .person__role {
    margin: 0;
    font-family: "Nunito", sans-serif;
    font-size: 19px;
    color: var(--muted);
    line-height: 1.1;
  }
  .contact {
    position: absolute;
    left: 394px;
    width: 280px;
    display: flex;
    align-items: center;
  }
  .contact__icon {
    width: 34px;
    height: 34px;
    flex: none;
  }
  .contact__text {
    margin-left: 30px;
    font-family: "Nunito", sans-serif;
    font-size: 16.5px;
    line-height: 1.05;
    color: var(--ink);
    white-space: nowrap;
  }
  .contact--address { top: 181px; }
  .contact--email { top: 230px; }
  .contact--phone { top: 278px; }
  .contact--web { top: 331px; }
  .rule {
    position: absolute;
    left: 458px;
    width: 35px;
    height: 2px;
    background: var(--line);
  }
  .rule--1 { top: 222px; }
  .rule--2 { top: 268px; }
  .rule--3 { top: 324px; }
</style>
</head>
<body>
<main class="canvas">
  <section class="card card--front" aria-label="Brand side">
    <h1 class="brand-name"><span class="brand-name__main">Veluxa</span><span class="brand-name__sub">Bone &amp; Motion</span></h1>
  </section>

  <section class="card card--back" aria-label="Contact side">
    <p class="brand-name"><span class="brand-name__main">Veluxa</span><span class="brand-name__sub">Bone &amp; Motion</span></p>
    <div class="divider"></div>

    <div class="person">
      <h2 class="person__name">MARLOWE</h2>
      <p class="person__role">CEO</p>
    </div>

    <div class="contact contact--address">
      <svg class="contact__icon" viewBox="0 0 34 34" aria-hidden="true">
        <circle cx="17" cy="17" r="16" fill="none" stroke="#a8a8a8" stroke-width="1"/>
        <path d="M9 17 L17 10 L25 17 M11.5 15.5 V24 H15 V19.5 H19 V24 H22.5 V15.5" fill="none" stroke="#9a9a9a" stroke-width="1.8" stroke-linejoin="round"/>
      </svg>
      <div class="contact__text">Street Address Here<br>Singapore, 2222</div>
    </div>
    <div class="rule rule--1"></div>

    <div class="contact contact--email">
      <svg class="contact__icon" viewBox="0 0 34 34" aria-hidden="true">
        <circle cx="17" cy="17" r="16" fill="none" stroke="#a8a8a8" stroke-width="1"/>
        <rect x="9" y="11.5" width="16" height="11" fill="none" stroke="#9a9a9a" stroke-width="1.6"/>
        <path d="M9 11.5 L17 18 L25 11.5 M9 22.5 L15 17 M25 22.5 L19 17" fill="none" stroke="#9a9a9a" stroke-width="1.4"/>
      </svg>
      <div class="contact__text">urname@email.com</div>
    </div>
    <div class="rule rule--2"></div>

    <div class="contact contact--phone">
      <svg class="contact__icon" viewBox="0 0 34 34" aria-hidden="true">
        <circle cx="17" cy="17" r="16" fill="none" stroke="#a8a8a8" stroke-width="1"/>
        <path d="M9 14 Q17 8 25 14 L23.5 16 L20.5 15 V13.5 Q17 12.5 13.5 13.5 V15 L10.5 16 Z" fill="#9a9a9a"/>
        <rect x="11" y="17.5" width="12" height="7" rx="1.5" fill="#9a9a9a"/>
        <circle cx="17" cy="21" r="1.8" fill="#ffffff"/>
      </svg>
      <div class="contact__text">+18 5550 1234 5678<br>+18 5550 8765 4321</div>
    </div>
    <div class="rule rule--3"></div>

    <div class="contact contact--web">
      <svg class="contact__icon" viewBox="0 0 34 34" aria-hidden="true">
        <circle cx="17" cy="17" r="16" fill="none" stroke="#a8a8a8" stroke-width="1"/>
        <circle cx="17" cy="17" r="8.5" fill="none" stroke="#9a9a9a" stroke-width="1.6"/>
        <ellipse cx="17" cy="17" rx="3.8" ry="8.5" fill="none" stroke="#9a9a9a" stroke-width="1.2"/>
        <path d="M8.5 17 H25.5 M10 12.5 H24 M10 21.5 H24" stroke="#9a9a9a" stroke-width="1.2"/>
      </svg>
      <div class="contact__text">www.websitename.com</div>
    </div>
  </section>
</main>
</body>
</html>
```